Webbanner-Design für Fachhandel für Medizinprodukte
Zielgruppe
wir sind ein Fachhandel für Medizinprodukte.
Aufgabenstellung
-Slider / Banner
-1920 x 340
-Es muss ein intersannter Satz auf dem Bild sein, der einläd zu klicken.
-https://www.korvantiq.de/
- folgender Artikel soll beworben werden:
-https://www.korvantiq.de/fingerpulsoximeter-tq418-pulsoximeter-weiss-2916
-Design soll gut zur Seite passen.
-Das Bild kann von der Seite verwendet werden.
-Gerne können zusätzlich auch Stockbilder verarbeitet werden.

```html
<!DOCTYPE html>
<html lang="de">
<head>
<meta charset="utf-8">
<title>KORVANTIQ – Fingerpulsoximeter TQ418</title>
<link rel="stylesheet" href="https://fonts.googleapis.com/css2?family=Montserrat:ital,wght@0,700;0,800;1,800&display=swap">
<style>
  :root {
    --stage-bg: #e0e0df;
    --banner-bg: #efefef;
    --brand-green: #45b04b;
    --ink: #1f1f1f;
    --white: #ffffff;
    --device-light: #fafafa;
    --device-shade: #d6d6d6;
  }
  * { margin: 0; padding: 0; box-sizing: border-box; }
  html, body {
    width: 1200px;
    height: 495px;
    overflow: hidden;
    background: var(--stage-bg);
    font-family: "Montserrat", Arial, sans-serif;
  }
  .banner {
    position: absolute;
    left: 90px;
    top: 157px;
    width: 1021px;
    height: 180px;
    background: var(--banner-bg);
    overflow: hidden;
  }
  .product-visual {
    position: absolute;
    left: 45px;
    top: 19px;
    width: 230px;
    height: 140px;
    border-radius: 10px;
    background: radial-gradient(ellipse at 50% 55%, var(--device-light) 0%, #eaeaea 60%, var(--device-shade) 100%);
  }
  .product-code {
    position: absolute;
    left: 155px;
    top: 32px;
    font-size: 26px;
    font-weight: 700;
    color: var(--ink);
    letter-spacing: 0.5px;
  }
  .headline-band {
    position: absolute;
    left: 0;
    top: 0;
    width: 1021px;
    height: 180px;
  }
  .headline-band polygon { fill: var(--brand-green); }
  .headline {
    position: absolute;
    left: 313px;
    top: 18px;
    width: 480px;
    text-align: center;
    color: var(--white);
    font-size: 66px;
    font-weight: 800;
    font-style: italic;
    line-height: 69px;
    letter-spacing: 0.5px;
  }
  .brand-name {
    position: absolute;
    left: 825px;
    top: 30px;
    font-size: 19px;
    font-weight: 700;
    color: var(--ink);
    letter-spacing: 0.5px;
  }
  .shop-button {
    position: absolute;
    left: 806px;
    top: 108px;
    width: 184px;
    height: 50px;
    border-radius: 8px;
    background: var(--brand-green);
    color: var(--white);
    font-size: 16px;
    font-weight: 700;
    display: flex;
    align-items: center;
    justify-content: center;
    text-decoration: none;
    box-shadow: 0 3px 8px rgba(0,0,0,0.15);
  }
</style>
</head>
<body>
  <div class="banner">
    <div class="product-visual" role="img" aria-label="Weißes Fingerpulsoximeter TQ418 mit beleuchtetem Display, einmal stehend und einmal liegend"></div>
    <div class="product-code">TQ418</div>

    <svg class="headline-band" viewBox="0 0 1021 180" aria-hidden="true">
      <polygon points="310,0 793,0 764,180 283,180"/>
    </svg>
    <h1 class="headline">SCHNELL<br>&amp; GENAUE</h1>

    <div class="brand-name">KORVANTIQ</div>

    <a class="shop-button" href="https://www.korvantiq.de/fingerpulsoximeter-tq418-pulsoximeter-weiss-2916">Jetzt Einkaufen</a>
  </div>
</body>
</html>
```